Brookvane Consulting Business Card Design

Business Card Design for Brookvane Consulting. Brookvane Consulting is a boutique consultancy based in Atlanta, GA., that specializes in marketing strategy, organization planning, and leadership development. We provide solutions for small businesses and startups as well as Vantage 300 companies.

http://brookvaneconsulting.com/

Target Market(s)

We provide solutions for small businesses and startups as well as Vantage 300 companies.

Industry/Entity Type

Consulting

Contact Information for Business Card

Two sided business card with priority on contact information, logo, tag line (Guidance to Plan Well, Lead Well, Grow Further)

Colors

Designer to choose colors to be used in the design.

Requirements
Must have
• contact information, logo, tag line (Guidance to Plan Well, Lead Well, Grow Further)
• Simple no over communication.
Nice to have
• I would like to see different placements of logo and creative use of both sides of the card
Should not have
• Do not put too much information on the card.

```html
<!DOCTYPE html>
<html lang="en">
<head>
<meta charset="utf-8">
<title>Brookvane Consulting Business Card</title>
<link href="https://fonts.googleapis.com/css2?family=Lato:wght@400;700&family=Courgette&display=swap" rel="stylesheet">
<style>
  :root {
    --canvas-bg: #3a3330;
    --card-black: #141414;
    --card-pattern: #1e1e1e;
    --ink-white: #ffffff;
    --ink-soft: #d9d9d9;
    --band-text: #111111;
  }
  * { margin: 0; padding: 0; box-sizing: border-box; }
  html, body {
    width: 1200px; height: 769px; overflow: hidden;
    background: var(--canvas-bg);
    font-family: "Lato", sans-serif;
  }
  .canvas { position: relative; width: 1200px; height: 769px; }
  .card {
    position: absolute; top: 234px;
    width: 525px; height: 300px;
    background: var(--card-black);
    border-radius: 4px;
    box-shadow: 0 10px 30px rgba(0,0,0,.45);
    overflow: hidden;
    color: var(--ink-white);
  }
  .card-front { left: 45px; }
  .card-back { left: 630px; }

  .wordmark {
    position: absolute;
    font-family: "Lato", sans-serif; font-weight: 700;
    color: var(--ink-white); line-height: 1.05; letter-spacing: .5px;
  }
  .card-front .wordmark { left: 34px; top: 100px; font-size: 30px; }
  .card-back .wordmark { left: 0; right: 0; top: 108px; text-align: center; font-size: 40px; }

  .holder { position: absolute; right: 40px; top: 36px; text-align: center; }
  .holder-name { font-family: "Courgette", cursive; font-size: 22px; line-height: 1.2; }
  .holder-title { font-size: 13px; color: var(--ink-soft); margin-top: 2px; }

  .contact-list {
    position: absolute; left: 34px; top: 184px;
    list-style: none; font-size: 13px; color: var(--ink-soft);
  }
  .contact-list li { display: flex; align-items: center; gap: 8px; height: 18px; white-space: nowrap; }
  .contact-list svg { width: 11px; height: 11px; fill: var(--ink-soft); flex: none; }

  .tagline-band {
    position: absolute; left: 0; bottom: 22px;
    width: 410px; height: 26px;
    background: var(--ink-white); color: var(--band-text);
    font-size: 13.5px; display: flex; align-items: center; padding-left: 34px;
    white-space: nowrap;
  }

  .back-pattern {
    position: absolute; inset: 0;
    background: linear-gradient(135deg, var(--card-pattern), var(--card-black) 60%, var(--card-pattern));
  }
</style>
</head>
<body>
<main class="canvas">
  <section class="card card-front">
    <div class="wordmark">Brookvane<br>Consulting</div>

    <div class="holder">
      <div class="holder-name">Darren Whitlock</div>
      <div class="holder-title">Founder/Managing Director</div>
    </div>

    <ul class="contact-list">
      <li>
        <svg viewBox="0 0 12 12"><path d="M2.5 1l2 2.2-1 1.3c.7 1.5 2 2.8 3.5 3.5l1.3-1 2.2 2-1.2 1.8C5 10.5 1.5 7 .8 2.2z"/></svg>
        424-555-0193
      </li>
      <li>
        <svg viewBox="0 0 12 12"><path d="M0 2h12v8H0z M1 3l5 3.5L11 3v-.2H1z" fill-rule="evenodd"/></svg>
        darren@brookvaneconsulting.com
      </li>
      <li>
        <svg viewBox="0 0 12 12"><circle cx="6" cy="6" r="5.5"/></svg>
        brookvaneconsulting.com
      </li>
    </ul>

    <div class="tagline-band">Guidance to Plan Well, Lead Well, Grow Further</div>
  </section>

  <section class="card card-back">
    <div class="back-pattern" role="img" aria-label="Subtle dark geometric pattern of triangles and lined boxes covering the card"></div>
    <div class="wordmark">Brookvane<br>Consulting</div>
  </section>
</main>
</body>
</html>
```